TK Homes - Stone Dorf Design

Looking for a double sides design, 1 side for my realestate and the other for home building. ( TK Homes on 1 side, Stone Dorf card on the other Side
Side 1 - Marek Tove ~ Vox Realty logo and Company ( the Property quarter )
Marek Tove
Marek@Marektove.example
IG - Marek_Bzq_Realtor
FB - marekt
Cell - 5558130467
3847 61 St Nw

Side 2
Marek Tove
5558130467
IG - Stonedorf_Bzq
Stonedorfdev@mailbox.example

Target Market(s)

Home buyers/ sellers

Industry/Entity Type

Home builders - Realestate

Contact Information for Business Card

Above

Requirements
Must have
• Black OR White background - my information -

```html
<!DOCTYPE html>
<html lang="en">
<head>
<meta charset="utf-8">
<title>TK Homes · Stone Dorf Design – Business Cards</title>
<link href="https://fonts.googleapis.com/css2?family=Tinos:wght@400;700&display=swap" rel="stylesheet">
<style>
  :root {
    --backdrop: #242424;
    --card: #1f1f24;
    --blue: #1a6fc0;
    --gold: #f5c842;
    --white: #ffffff;
  }
  * { box-sizing: border-box; margin: 0; padding: 0; }
  html, body { width: 1200px; height: 780px; overflow: hidden; background: var(--backdrop); }
  body {
    font-family: "Tinos", "Times New Roman", serif;
    display: flex; align-items: center; justify-content: center; gap: 70px;
  }
  .card {
    position: relative;
    width: 390px; height: 680px;
    background: var(--card);
    border-left: 5px solid var(--gold);
    box-shadow: 0 10px 30px rgba(0,0,0,.45);
    padding: 60px 40px 50px 40px;
    display: flex; flex-direction: column;
  }
  .brand-mark {
    text-align: center;
    font-weight: 700;
    color: var(--blue);
  }
  .brand-mark--realty { font-size: 34px; letter-spacing: 2px; margin-top: 40px; }
  .brand-mark--builder { font-size: 38px; letter-spacing: 3px; }
  .brand-mark__sub { display: block; font-size: 16px; letter-spacing: 5px; margin-top: 6px; }
  .brand-mark__dot {
    display: block; width: 18px; height: 18px; border-radius: 50%;
    background: var(--blue); margin: 0 auto 14px;
  }
  .contact { margin-top: auto; padding-left: 50px; }
  .contact__name { font-size: 40px; font-weight: 700; line-height: 1; }
  .contact__first { color: var(--blue); }
  .contact__last { color: var(--gold); }
  .contact__title { color: var(--white); font-weight: 700; font-size: 19px; margin: 4px 0 0 14px; }
  .contact__address { color: var(--white); font-size: 19px; margin: 26px 0 14px 30px; }
  .contact__list { list-style: none; margin-top: 8px; }
  .contact__item {
    display: flex; align-items: center; gap: 10px;
    color: var(--white); font-size: 18px; line-height: 1.55;
  }
  .contact__item--plain { padding-left: 26px; }
  .icon { width: 16px; height: 16px; flex: none; fill: var(--blue); }
  .icon--ring { fill: none; stroke: var(--blue); stroke-width: 2; }
</style>
</head>
<body>

  <section class="card card--realty">
    <div class="brand-mark brand-mark--realty">MAREK TOVE</div>
    <div class="contact">
      <p class="contact__name"><span class="contact__first">Marek</span> <span class="contact__last">Tove</span></p>
      <p class="contact__title">Director</p>
      <p class="contact__address">3847 61 St Nw</p>
      <ul class="contact__list">
        <li class="contact__item contact__item--plain">5558130467</li>
        <li class="contact__item">
          <svg class="icon" viewBox="0 0 16 16"><path d="M3 1l3 3-2 2c1 2 3 4 5 5l2-2 3 3-2 3C6 14 2 10 1 3z"/></svg>marekt</li>
        <li class="contact__item">
          <svg class="icon" viewBox="0 0 16 16"><circle cx="8" cy="8" r="7"/></svg>Marek_Bzq_Realtor</li>
        <li class="contact__item">
          <svg class="icon" viewBox="0 0 16 16"><rect x="1" y="1" width="14" height="14"/></svg>Marek@Marektove.example</li>
        <li class="contact__item">
          <svg class="icon" viewBox="0 0 16 16"><path d="M1 3h14v10H1z M1 3l7 6 7-6" fill="none" stroke="#1a6fc0" stroke-width="1.6"/></svg>www.marektove.example</li>
      </ul>
    </div>
  </section>

  <section class="card card--builder">
    <div class="brand-mark brand-mark--builder">
      <span class="brand-mark__dot"></span>
      STONE DORF
      <span class="brand-mark__sub">DEVELOPMENTS</span>
    </div>
    <div class="contact">
      <p class="contact__name"><span class="contact__first">Marek</span> <span class="contact__last">Tove</span></p>
      <p class="contact__title">Director</p>
      <ul class="contact__list">
        <li class="contact__item">
          <svg class="icon" viewBox="0 0 16 16"><path d="M3 1l3 3-2 2c1 2 3 4 5 5l2-2 3 3-2 3C6 14 2 10 1 3z"/></svg>5558130467</li>
        <li class="contact__item">
          <svg class="icon" viewBox="0 0 16 16"><circle cx="8" cy="8" r="7"/></svg>Stonedorf_Bzq</li>
        <li class="contact__item">
          <svg class="icon" viewBox="0 0 16 16"><path d="M1 3h14v10H1z M1 3l7 6 7-6" fill="none" stroke="#1a6fc0" stroke-width="1.6"/></svg>Stonedorfdev@mailbox.example</li>
      </ul>
    </div>
  </section>

</body>
</html>
```